Business Card- Can you make it cool vs boring!

Need a refresh on my business card! Want it to be modern but simple, classic and a pop of coolness! we do senior living and it is boring. but that doesn't mean our business card have to look boring! Open to two sided cards. our website is www.Dunmere-PK.com

Target Market(s)

capital market

Industry/Entity Type

senior housing/ real estate

Contact Information for Business Card

logo/ name/ cell/ address/ www.Dunmere-PK.com/ space for a QR code

Requirements
Must have
• maybe a QR code (do not make prominent I may not use the QR so design where it can be taken out) that link to more about us/ landing page. needs to be modern but clean
Should not have
• clip art or script

```html
<!DOCTYPE html>
<html lang="en">
<head>
<meta charset="utf-8">
<title>Dunmere Park – Business Card</title>
<link href="https://fonts.googleapis.com/css2?family=Poppins:wght@400;500;600&display=swap" rel="stylesheet">
<style>
  :root{
    --terracotta:#ad5028;
    --ink-grey:#707070;
    --rule-grey:#c9c9c9;
    --paper:#ffffff;
    --backdrop:#e8e3dc;
  }
  *{margin:0;padding:0;box-sizing:border-box}
  html,body{width:1189px;height:1200px;overflow:hidden}
  body{background:var(--backdrop);font-family:"Poppins",sans-serif;position:relative}

  .card{position:absolute;left:169px;width:851px;height:485px;border-radius:38px;overflow:hidden;
        box-shadow:0 6px 16px rgba(0,0,0,.18)}
  .card--front{top:112px;background:var(--paper)}
  .card--back{top:641px;background:var(--terracotta)}

  .brand{position:absolute;font-weight:500;white-space:nowrap}
  .card--front .brand{left:40px;top:210px;width:340px;text-align:center;font-size:42px;color:var(--terracotta);letter-spacing:.5px}
  .card--back .brand{left:0;right:0;top:200px;text-align:center;font-size:78px;color:var(--paper);letter-spacing:1px}

  .divider{position:absolute;left:412px;top:160px;width:2px;height:166px;background:var(--rule-grey)}

  .person{position:absolute;left:454px;top:158px}
  .person__name{font-size:29px;font-weight:600;color:var(--terracotta);line-height:1.1}
  .person__title{font-size:16px;color:var(--ink-grey);margin-top:2px}
  .person__rule{width:66px;height:3px;background:var(--terracotta);margin-top:10px}

  .contacts{position:absolute;left:454px;top:243px;list-style:none}
  .contacts li{display:flex;align-items:center;height:29px;font-size:22px;color:var(--ink-grey);line-height:1}
  .contacts svg{width:24px;height:24px;margin-right:12px;flex:none}

  .address-band{position:absolute;left:0;top:406px;width:100%;height:45px;background:var(--terracotta);
                color:var(--paper);font-size:20px;font-weight:500;display:flex;align-items:center;justify-content:center}
</style>
</head>
<body>

<section class="card card--front">
  <div class="brand">Dunmere Park</div>
  <div class="divider"></div>

  <div class="person">
    <div class="person__name">Owen R Hale</div>
    <div class="person__title">CEO</div>
    <div class="person__rule"></div>
  </div>

  <ul class="contacts">
    <li>
      <svg viewBox="0 0 24 24" aria-hidden="true"><circle cx="12" cy="12" r="12" fill="#ad5028"/>
        <path d="M8.6 6.5l1.8-.4 1.1 2.7-1.3 1c.6 1.4 1.6 2.4 3 3l1-1.3 2.7 1.1-.4 1.8c-.2.7-.9 1.1-1.6 1-3.8-.6-6.7-3.5-7.3-7.3-.1-.7.3-1.4 1-1.6z" fill="#fff"/></svg>
      (555) 014-27380
    </li>
    <li>
      <svg viewBox="0 0 24 24" aria-hidden="true"><circle cx="12" cy="12" r="12" fill="#ad5028"/>
        <rect x="6.5" y="8" width="11" height="8" rx="1" fill="none" stroke="#fff" stroke-width="1.5"/>
        <path d="M6.8 8.5L12 12.5l5.2-4M6.8 15.5l3.7-3.3M17.2 15.5l-3.7-3.3" fill="none" stroke="#fff" stroke-width="1.3"/></svg>
      hello@dunmerepark.com
    </li>
    <li>
      <svg viewBox="0 0 24 24" aria-hidden="true"><circle cx="12" cy="12" r="12" fill="#ad5028"/>
        <g fill="none" stroke="#fff" stroke-width="1.2"><circle cx="12" cy="12" r="5.5"/><ellipse cx="12" cy="12" rx="2.3" ry="5.5"/><path d="M6.5 12h11M7.3 9.2h9.4M7.3 14.8h9.4"/></g></svg>
      www.Dunmere-PK.com
    </li>
  </ul>

  <div class="address-band">418 Linden Court, Suite #210</div>
</section>

<section class="card card--back">
  <div class="brand">Dunmere Park</div>
</section>

</body>
</html>
```